"Inkvale" printing shop

-The design must be based around the attached HPID (home page information design) called "Inkvale - HPID".

The table boxes are just for approximate placement of information – you DON'T have to box everything in and you can arrange these. All fonts used in the HPID are only examples - you can use any Google font you wish.

- Information only is in orange text. Copy to go on the design in black text. Some instructions are in the HPID. Please be creative!

-The design needs to be modern. Colours are to be consistent with their new logo or complement it. Keep it clean and simple, you don't need to use lots of colours. Use lots of white.

- images / icons for the site need to be relevant and high quality, but they must also be free images or icons. I have attached a few examples that could be used.

Width of content will be 1100 pixels when implemented as a web page. Header height (without nav bar) 150-200 pixels.

If your design is chosen the winning PSD file will have to be provided as follows…
1. Canvas size of 2000px x 2000px - 72ppi in Adobe Photoshop (CS5 compatible)
2. Width of content section is 1100px wide - centered in the canvas
3. Any button rollovers/hovers in the PSD as hidden layers.
4. All fonts used must be Google fonts.
5. You will need to supply the chosen home page plus one example page (example page as a style guide for how all other pages will look). Example page is only the header and navigational bar at the top, an empty sector in the middle with a column (190 px wide) which can be left or right aligned which means the main sector is 910 pixels wide, and then the footer at the bottom of the page

Checklist - http://pagebuildertally.example/

Examples of some websites that have great design... don't copy them please but they are similar in look to what we are after....
http://www.rookfenly.example/

Industry/Entity Type

Printing

Font styles to use
Serif
Sans Serif

Requirements
Should not have
• Drop shadows, comic sans font

```html
<!DOCTYPE html>
<html lang="en">
<head>
<meta charset="utf-8">
<title>Inkvale – Printing Shop</title>
<link href="https://fonts.googleapis.com/css2?family=Roboto+Condensed:wght@400;700&family=Open+Sans:wght@400;600;700&display=swap" rel="stylesheet">
<style>
:root{
  --ink:#1c1c1c;
  --text:#3a3a3a;
  --muted:#777;
  --accent:#c8102e;
  --panel:#e4e4e4;
  --soft:#f3f3f3;
  --white:#fff;
  --footer:#2a2a2a;
  --footer-line:#444;
}
*{box-sizing:border-box;margin:0;padding:0}
html,body{width:784px;height:1200px;overflow:hidden;background:var(--white)}
body{font-family:"Open Sans",sans-serif;color:var(--text);font-size:8px;position:relative}
.heading{font-family:"Roboto Condensed",sans-serif}

/* header */
.site-header{position:absolute;top:0;left:0;width:784px;height:57px;padding:0 78px;display:flex;align-items:center}
.brand{display:flex;align-items:center;gap:6px;width:150px}
.brand-dot{width:26px;height:26px;border-radius:50%;background:var(--ink)}
.brand-name{font-family:"Roboto Condensed",sans-serif;font-weight:700;font-size:24px;color:var(--ink)}
.tagline{flex:1}
.tagline h1{font-family:"Roboto Condensed",sans-serif;font-size:17px;font-weight:700;color:var(--ink);letter-spacing:.3px}
.tagline p{font-size:7px;color:var(--muted);margin-top:2px}
.header-meta{text-align:right;font-size:7px;color:var(--text)}
.utility{display:flex;gap:8px;justify-content:flex-end;margin-bottom:6px}
.contact-line{display:flex;align-items:center;justify-content:flex-end;gap:4px;margin-top:3px}
.contact-line svg{width:9px;height:9px}

/* nav */
.main-nav{position:absolute;top:57px;left:0;width:784px;height:14px;background:var(--soft);border-top:1px solid #ddd;border-bottom:1px solid #ddd;display:flex;align-items:center;padding:0 78px;gap:6px;font-size:7px;color:var(--ink)}
.main-nav .sep{color:var(--accent)}

/* hero */
.hero{position:absolute;top:71px;left:0;width:784px;height:216px;background:linear-gradient(120deg,#4a3a35 0%,#7a5a48 35%,#5d6a7a 65%,#3d3a3f 100%)}
.hero-title{position:absolute;left:150px;top:72px;width:460px;font-family:"Roboto Condensed",sans-serif;font-weight:700;font-size:27px;line-height:1.15;color:var(--white);text-transform:uppercase}
.hero-dots{position:absolute;bottom:12px;left:50%;transform:translateX(-50%);display:flex;gap:5px}
.hero-dots span{width:6px;height:6px;border-radius:50%;background:rgba(255,255,255,.5)}
.hero-dots span:first-child{background:var(--white)}

/* service tiles */
.services{position:absolute;top:287px;left:0;width:784px;height:300px;background:var(--panel)}
.tiles{position:absolute;top:48px;left:78px;width:627px;display:grid;grid-template-columns:repeat(3,1fr);column-gap:28px;row-gap:24px}
.tile{height:62px;background:var(--white);display:flex;align-items:center;padding:0 14px;gap:14px}
.tile svg{width:36px;height:30px;flex:none}
.tile-label{font-family:"Roboto Condensed",sans-serif;font-size:9px;text-transform:uppercase;color:var(--ink)}

/* features */
.features{position:absolute;top:587px;left:0;width:784px;height:340px;background:var(--soft);padding:38px 78px 0}
.feature-grid{display:grid;grid-template-columns:1fr 1fr;column-gap:40px;row-gap:22px}
.feature{display:flex;gap:10px}
.feature-icon{width:40px;height:40px;border-radius:50%;background:var(--ink);flex:none;display:flex;align-items:center;justify-content:center}
.feature-icon svg{width:20px;height:20px}
.feature h3{font-family:"Roboto Condensed",sans-serif;font-size:11.5px;font-weight:700;color:var(--ink);margin-bottom:3px}
.feature p{font-size:7px;line-height:1.45;color:var(--text)}
.more{display:block;text-align:right;font-weight:700;font-size:7px;color:var(--ink);margin-top:3px}

/* quote */
.quote{position:absolute;top:927px;left:0;width:784px;height:135px;padding:26px 78px 0;display:flex;gap:40px}
.quote-intro{width:150px}
.quote-intro h2{font-family:"Roboto Condensed",sans-serif;font-size:16px;font-weight:700;color:var(--ink);margin-bottom:6px}
.quote-intro p{font-size:7px;line-height:1.5}
.quote-form{flex:1;display:grid;grid-template-columns:1fr 1fr;column-gap:12px}
.field{height:16px;border:1px solid #ccc;font-size:7px;color:var(--muted);padding:3px 5px;margin-bottom:6px}
.field.area{height:38px}
.submit{justify-self:end;background:var(--ink);color:var(--white);font-size:7px;font-weight:700;padding:4px 12px}

/* footer */
.site-footer{position:absolute;top:1062px;left:0;width:784px;height:138px;background:var(--footer);padding:16px 78px 0;color:#ccc}
.site-footer h2{font-family:"Roboto Condensed",sans-serif;font-size:14px;color:var(--white);font-weight:700;padding-bottom:8px;border-bottom:1px solid var(--footer-line)}
.footer-links{display:flex;gap:7px;font-size:7px;margin-top:12px;flex-wrap:wrap}
.footer-links span::before{content:"» ";color:var(--accent)}
.footer-bottom{position:absolute;left:78px;right:78px;bottom:14px;display:flex;justify-content:space-between;align-items:center;font-size:7px;border-top:1px solid var(--footer-line);padding-top:10px}
.social{display:flex;gap:5px;align-items:center}
.social i{width:11px;height:11px;border-radius:50%;background:#666;display:block}
</style>
</head>
<body>

<header class="site-header">
  <div class="brand"><span class="brand-dot"></span><span class="brand-name">Inkvale</span></div>
  <div class="tagline">
    <h1>DUPLICATION IS OUR VOCATION</h1>
    <p>Professional Photocopying · Digital &amp; Film Processing, Design &amp; Printing</p>
  </div>
  <div class="header-meta">
    <div class="utility"><span>Home</span><span>About</span><span>Free Quote</span><span>Contact</span></div>
    <div class="contact-line"><svg viewBox="0 0 10 10"><rect width="10" height="10" fill="#1c1c1c"/><path d="M3 2.5c0 2.5 2 4.5 4.5 4.5l.5-1-1.5-.8-.6.6c-.9-.4-1.5-1-1.9-1.9l.6-.6L3.8 2z" fill="#fff"/></svg>07 555 0148</div>
    <div class="contact-line"><svg viewBox="0 0 10 10"><rect width="10" height="10" fill="#1c1c1c"/><path d="M5 2a2 2 0 0 0-2 2c0 1.5 2 4 2 4s2-2.5 2-4a2 2 0 0 0-2-2z" fill="#fff"/></svg>12 Kestrel Lane, Greerton, Tauranga</div>
  </div>
</header>

<nav class="main-nav">
  <span>Photocopying</span><span class="sep">|</span><span>Printing</span><span class="sep">|</span><span>Laminating</span><span class="sep">|</span><span>Business cards</span><span class="sep">|</span><span>Typing services</span><span class="sep">|</span><span>Film processing</span><span class="sep">|</span><span>Photo Printing</span><span class="sep">|</span><span>Passport Photos</span><span class="sep">|</span><span>Image Restoration</span><span class="sep">|</span><span>Printer Supplies</span>
</nav>

<section class="hero" role="img" aria-label="Photo of colourful printed documents and photographs spread on a desk">
  <h2 class="hero-title">Digital printing, laminating and photocopying services throughout Tauranga</h2>
  <div class="hero-dots"><span></span><span></span><span></span></div>
</section>

<section class="services">
  <div class="tiles">
    <div class="tile"><svg viewBox="0 0 36 30"><rect x="3" y="8" width="30" height="14" fill="#1c1c1c"/><rect x="8" y="3" width="20" height="6" fill="none" stroke="#1c1c1c" stroke-width="2"/><rect x="9" y="20" width="18" height="7" fill="#fff" stroke="#1c1c1c" stroke-width="2"/></svg><span class="tile-label">Photo copying</span></div>
    <div class="tile"><svg viewBox="0 0 36 30"><rect x="6" y="4" width="22" height="22" fill="none" stroke="#1c1c1c" stroke-width="2"/><rect x="10" y="8" width="22" height="18" fill="#1c1c1c"/></svg><span class="tile-label">Laminating &amp; Binding</span></div>
    <div class="tile"><svg viewBox="0 0 36 30"><rect x="4" y="10" width="28" height="12" fill="#1c1c1c"/><rect x="10" y="3" width="16" height="8" fill="none" stroke="#1c1c1c" stroke-width="2"/><rect x="10" y="19" width="16" height="8" fill="#fff" stroke="#1c1c1c" stroke-width="2"/></svg><span class="tile-label">Digital printing</span></div>
    <div class="tile"><svg viewBox="0 0 36 30"><rect x="4" y="4" width="28" height="22" fill="#1c1c1c"/><g fill="#fff"><rect x="7" y="7" width="3" height="3"/><rect x="7" y="13" width="3" height="3"/><rect x="7" y="19" width="3" height="3"/><rect x="26" y="7" width="3" height="3"/><rect x="26" y="13" width="3" height="3"/><rect x="26" y="19" width="3" height="3"/><rect x="13" y="8" width="10" height="14"/></g></svg><span class="tile-label">Film processing</span></div>
    <div class="tile"><svg viewBox="0 0 36 30"><rect x="4" y="5" width="28" height="20" fill="none" stroke="#1c1c1c" stroke-width="2"/><circle cx="13" cy="13" r="3.5" fill="#1c1c1c"/><rect x="8" y="18" width="10" height="3" fill="#1c1c1c"/><rect x="20" y="11" width="9" height="2" fill="#1c1c1c"/><rect x="20" y="16" width="9" height="2" fill="#1c1c1c"/></svg><span class="tile-label">Business cards</span></div>
    <div class="tile"><svg viewBox="0 0 36 30"><rect x="4" y="8" width="28" height="17" fill="#1c1c1c"/><rect x="12" y="4" width="10" height="5" fill="#1c1c1c"/><circle cx="18" cy="16.5" r="5" fill="#fff"/><circle cx="18" cy="16.5" r="2.5" fill="#1c1c1c"/></svg><span class="tile-label">Photo printing</span></div>
  </div>
</section>

<section class="features">
  <div class="feature-grid">
    <div class="feature"><div class="feature-icon"><svg viewBox="0 0 20 20"><rect x="2" y="6" width="16" height="8" fill="#fff"/><rect x="5" y="12" width="10" height="5" fill="#fff"/></svg></div><div><h3>Cost Effective Photocopying</h3><p>No matter the quantity of copies you need or the size of your project, you can rely on us to deliver a fast, tidy and affordable service.</p><span class="more">Click Here »</span></div></div>
    <div class="feature"><div class="feature-icon"><svg viewBox="0 0 20 20"><rect x="3" y="4" width="14" height="10" fill="#fff"/><rect x="7" y="15" width="6" height="2" fill="#fff"/></svg></div><div><h3>Personal Desktop Publishing</h3><p>From personalised brochures, posters and birthday and special occasion cards to top quality, cheap business cards – you get it all!</p><span class="more">Click Here »</span></div></div>
    <div class="feature"><div class="feature-icon"><svg viewBox="0 0 20 20"><rect x="3" y="7" width="14" height="7" fill="#fff"/><rect x="6" y="3" width="8" height="4" fill="#fff"/></svg></div><div><h3>All Digital Format Printing</h3><p>Either email us your file or bring it into the store and we can give you the print you need. All prints are to the highest quality.</p><span class="more">Click Here »</span></div></div>
    <div class="feature"><div class="feature-icon"><svg viewBox="0 0 20 20"><circle cx="10" cy="10" r="7" fill="#fff"/><circle cx="10" cy="10" r="2" fill="#1c1c1c"/></svg></div><div><h3>Film Photo Processing</h3><p>Bring in your film to the store and we will work with you to get the high quality print for your purpose and needs. We work with it all!</p><span class="more">Click Here »</span></div></div>
    <div class="feature"><div class="feature-icon"><svg viewBox="0 0 20 20"><rect x="4" y="3" width="12" height="14" fill="#fff"/></svg></div><div><h3>Laminating &amp; Binding</h3><p>Either email us your file or bring it into the store and we can give you the finish you need. All jobs are to the highest quality.</p><span class="more">Click Here »</span></div></div>
    <div class="feature"><div class="feature-icon"><svg viewBox="0 0 20 20"><rect x="2" y="6" width="16" height="11" fill="#fff"/><circle cx="10" cy="11.5" r="3" fill="#1c1c1c"/></svg></div><div><h3>Quality Digital Photo Print</h3><p>Get your photos printed to your requirements – either from a file or from your digital camera. With a wide range of options you can get the print you want.</p><span class="more">Click Here »</span></div></div>
  </div>
</section>

<section class="quote">
  <div class="quote-intro">
    <h2>Get A Free Quote</h2>
    <p>...or talk to our team about your requirements. Please fill out the form below and we will contact you within a day.</p>
    <p style="margin-top:5px">You can now upload and send us your file for a free quote!</p>
  </div>
  <div class="quote-form">
    <div><div class="field">First Name</div><div class="field">Last Name</div><div class="field">Phone Number</div></div>
    <div><div class="field">Email</div><div class="field area">Message</div></div>
    <span></span><span class="submit">Submit</span>
  </div>
</section>

<footer class="site-footer">
  <h2>Quick Links</h2>
  <div class="footer-links"><span>Home</span><span>About</span><span>Photocopying</span><span>Printing</span><span>Laminating</span><span>Business Cards</span><span>Typing Services</span><span>Film Processing</span><span>Photo Printing</span><span>Passport Photos</span><span>Image Restoration</span><span>Printer Supplies</span><span>Free Quote</span><span>Contact</span></div>
  <div class="footer-bottom">
    <span>Copyright By Inkvale, 2015</span>
    <span class="social">Follow Us <i></i><i></i><i></i></span>
  </div>
</footer>

</body>
</html>
```